Brookvale Estates LLC stationary for a real estate property management company.

Create stationary (letterhead, envelopes, business cards) using Brookvale Estates LLC logo as primary creative element. Stationary design needs to be horizontal, leaving as much space as possible for correspondence copy. See attached Creative Brief and past stationary files for details.

Target Market(s)

Prospective apartment residents and current residents, vendors, and government agencies.

Industry/Entity Type

Property Management

Contact Information for Business Card

Business card employee title: Property Manager. Should include address, phone, fax, email, website, slogan, and Brookvale Estates logo.

Font styles to use
Sans Serif

Colors
0592cd
000000

Requirements
Must have
• Tone should be conservative, institutional, business (i.e. banking, finance, real estate). Must include: address, phone, fax, website, and slogan (see attached Creative Brief). Should be a horizontal design, leaving as much room as possible for letter correspondence copy.
Nice to have
• Please use an Arial or Helvetica style font.
Should not have
• Letterhead layout should leave as much room as possible for copy.

```html
<!DOCTYPE html>
<html lang="en">
<head>
<meta charset="UTF-8">
<title>Brookvale Estates LLC – Business Card</title>
<link href="https://fonts.googleapis.com/css2?family=Arimo:wght@400;700&display=swap" rel="stylesheet">
<style>
  :root {
    --backdrop: #2a2a2a;
    --card-white: #f7f7f7;
    --brand-blue: #0b72b5;
    --brand-blue-light: #1ab6e8;
    --brand-blue-deep: #0a66a0;
    --text-gray: #4a4a4a;
    --swoosh-gray: #4d4d4d;
    --divider: #9a9a9a;
    --white: #ffffff;
  }
  * { margin: 0; padding: 0; box-sizing: border-box; }
  html, body { width: 1200px; height: 960px; overflow: hidden; }
  body {
    background: var(--backdrop);
    font-family: "Arimo", Arial, Helvetica, sans-serif;
    position: relative;
  }
  .card {
    position: absolute;
    width: 600px;
    height: 342px;
    overflow: hidden;
  }
  .card-front { left: 302px; top: 129px; background: var(--card-white); }
  .card-back {
    left: 299px; top: 488px;
    background: linear-gradient(135deg, var(--brand-blue-light) 0%, var(--brand-blue-deep) 45%, #0b65a0 100%);
  }

  .brand-lockup {
    position: absolute;
    left: 50px; top: 128px;
    display: flex; align-items: center; gap: 10px;
  }
  .brand-dot {
    width: 16px; height: 16px; border-radius: 50%;
    background: var(--brand-blue);
  }
  .brand-name {
    color: var(--brand-blue);
    font-weight: 700;
    font-size: 21px;
    line-height: 1.15;
    letter-spacing: 0.5px;
  }

  .divider {
    position: absolute;
    left: 307px; top: 70px;
    width: 1px; height: 176px;
    background: var(--divider);
  }

  .contact {
    position: absolute;
    left: 330px; top: 72px;
    color: var(--text-gray);
    font-size: 14.5px;
    line-height: 19px;
  }
  .contact-name {
    color: var(--brand-blue);
    font-weight: 700;
    font-size: 21px;
    line-height: 24px;
  }
  .contact-title { font-size: 16px; line-height: 20px; margin-bottom: 7px; }
  .contact-address { margin-bottom: 6px; }
  .contact-line { display: flex; align-items: center; gap: 8px; }
  .contact-line svg { width: 14px; height: 14px; flex: none; }

  .swoosh { position: absolute; left: 0; bottom: 0; width: 600px; height: 70px; }

  .back-brand {
    position: absolute;
    left: 0; right: 0; top: 120px;
    display: flex; justify-content: center; align-items: center; gap: 14px;
  }
  .back-brand .brand-dot { width: 22px; height: 22px; background: var(--white); }
  .back-brand .brand-name { color: var(--white); font-size: 32px; }

  .slogan {
    position: absolute;
    left: 0; right: 0; top: 288px;
    text-align: center;
    color: var(--white);
    font-weight: 700;
    font-size: 16.5px;
  }
</style>
</head>
<body>

<section class="card card-front">
  <div class="brand-lockup">
    <span class="brand-dot"></span>
    <span class="brand-name">BROOKVALE<br>ESTATES LLC</span>
  </div>

  <div class="divider"></div>

  <div class="contact">
    <div class="contact-name">DANIEL HARPER</div>
    <div class="contact-title">Property Manager</div>
    <div class="contact-address">2750 Alder Creek Road #B210<br>Fresno, CA 93711</div>
    <div class="contact-line">
      <svg viewBox="0 0 14 14"><path fill="#0b72b5" d="M3 1l2.3 2.6-1.2 1.6c.8 1.7 2 2.9 3.7 3.7l1.6-1.2L12 10l-1 2.3C6 12.5 1.5 8 1.7 2z"/></svg>
      <span>559-214-7730</span>
    </div>
    <div class="contact-line">
      <svg viewBox="0 0 14 14"><rect x="3.5" y="1" width="7" height="4" fill="#0b72b5"/><rect x="1" y="5" width="12" height="6" rx="1" fill="#0b72b5"/><rect x="3.5" y="9" width="7" height="4" fill="#f7f7f7" stroke="#0b72b5"/></svg>
      <span>559-214-7731</span>
    </div>
    <div class="contact-line">
      <svg viewBox="0 0 14 14"><rect x="1" y="3" width="12" height="8" fill="#0b72b5"/><path d="M1.5 3.5L7 8l5.5-4.5" fill="none" stroke="#f7f7f7" stroke-width="1"/></svg>
      <span>daniel@brookvaleestates.us</span>
    </div>
    <div class="contact-line">
      <svg viewBox="0 0 14 14"><circle cx="7" cy="7" r="6" fill="#0b72b5"/><path d="M4 4.5c1.5 0 2 1 1.5 2s.5 2 1.5 2.5M9 3c-.5 1 .5 1.5 1.5 1.5" fill="none" stroke="#f7f7f7" stroke-width="1"/></svg>
      <span>www.brookvaleestates.us</span>
    </div>
  </div>

  <svg class="swoosh" viewBox="0 0 600 70" preserveAspectRatio="none">
    <path d="M0 28 Q250 90 600 40 L600 70 L0 70 Z" fill="#0b72b5"/>
    <path d="M0 8 Q240 58 600 36 Q250 72 0 22 Z" fill="#4d4d4d"/>
    <path d="M0 22 Q250 72 600 36 L600 40 Q250 84 0 26 Z" fill="#ffffff"/>
  </svg>
</section>

<section class="card card-back">
  <div class="back-brand">
    <span class="brand-dot"></span>
    <span class="brand-name">BROOKVALE ESTATES LLC</span>
  </div>
  <div class="slogan">Multifamily Property Management</div>
</section>

</body>
</html>
```